Update Existing Homepage

Here’s the scoop… we want to update our homepage here with a more modern look: wws.Plume-Harbor.com

I am NOT looking for a brand new design; as our site has many pages, and section. Instead I want a new more modern design based on the existing design (if that make sense)

Whatever new design…must match the rest of the site
I want the current header (menu and up) as well as the current footer to stay the same; it’s everything in between that has to change.

What I’m really looking for is:

- Better use of space
- Better emphasis on key components
- Addition of a new section (more about that below)
- More modern feel

By modern I mean the icons we use are getting a bit cheesy, the straight layout is also dated, etc

Here are the elements that I need to have on the page in ORDER OF IMPORTANCE:

1) ADVERTISING SPACE: while I don’t want huge flashing ads front and center, this being an information site, ads are our #1 source of revenue and as such are important. I would like to see several add slots of various sizes (standard sizes) throughout the page in eye catching spots (not hidden in the bottom right corner)

2) ARTICLES: articles are our main draw. If you look at the current design you will see there is a lead article at the top left of the page and then a series of other articles down the middle

3) NEWSLETTER SUBSCRIPTION BOX: need to have a section that is highly visible for people to subscribe to our newsletter (doesn’t have to be as big as the existing one)

4) BLOG POSTS (‘the experts say’ section): besides articles we also have blog posts. However I’m thinking we could combine the articles and the blog posts into 1 section titled “news” or something to save space. And the blog posts could just have an identifier at the beginning of the title such as “Blog: post title”

5) VIDEOS: don’t need to show a ton of vids, but would like room for 1 main video and a few suggestions of others.

What I have seen a bunch of new websites use is a type rotating ‘newsboard’, like the one on the zorbly homepage for example. Perhaps using an idea like that could be cool. You could feature 1 article, 1 blog post, 1 video, or something in it and have it rotate.

6) RESOURCES: This is something that is not ‘really’ currently on the homepage. By that I mean there is a “webmaster resources” section + a “webmaster tools” section but these are dated. Dated because we recently added a new directory to the site: http://resources.plume-harbor.com/ - so what I would like to do now is combine those 2 section; 1) invite people to check out the directory + submit there and 2) list a few of the newer entries (ie. new entries automatically get posted on the section of our homepage

7) FORUM DISCUSSIONS: if you look at the “Industry Discussions and Help” section, those are the latest discussions from our forums http://forums.plume-harbor.com/

That is it…good luck,

Tod

Target Market(s)

web professionals

Industry/Entity Type

Industry

Requirements
Must have
• see description
Nice to have
• see description
Should not have
• see description

```html
<!DOCTYPE html>
<html lang="en">
<head>
<meta charset="utf-8">
<title>Plume Harbor – Helping You Succeed Online</title>
<link href="https://fonts.googleapis.com/css2?family=Arimo:wght@400;700&display=swap" rel="stylesheet">
<style>
:root{
  --green:#a8c81a;
  --green-light:#d6ea5a;
  --green-dark:#7fa10e;
  --olive:#7c9a18;
  --blue:#4aa3e8;
  --blue-light:#8ccaf7;
  --link:#3d8fd6;
  --orange:#f39a1d;
  --text:#333;
  --muted:#666;
  --line:#e2e2e2;
  --ad:#d9d9d9;
  --ad-text:#999;
}
*{box-sizing:border-box;margin:0;padding:0}
html,body{width:711px;height:1200px;overflow:hidden;background:#fff;font-family:"Arimo",Arial,sans-serif;color:var(--text)}
.page{position:relative;width:711px;height:1200px}
.abs{position:absolute}
a{color:var(--link);text-decoration:none}

/* header */
.brand{left:95px;top:38px;font-size:20px;color:#333;display:flex;align-items:center;gap:6px}
.brand-dot{width:18px;height:18px;border-radius:50%;background:var(--green)}
.tagline{left:96px;top:61px;font-size:10.5px;color:#6e8a2a;letter-spacing:.5px}
.search{left:385px;top:20px;width:273px;height:25px;background:#f2f2f2;border:1px solid #ddd;border-radius:3px}
.search-field{position:absolute;left:30px;top:5px;width:155px;height:13px;background:#fff;border:1px solid #ccc}
.search-btn{position:absolute;right:0;top:0;width:60px;height:23px;background:linear-gradient(#e4f27a,var(--green));font-size:7.5px;color:#333;display:flex;align-items:center;justify-content:center;border-left:1px solid #bcd24a}
.lang{left:617px;top:58px;font-size:9px;color:#555;display:flex;align-items:center;gap:4px}
.lang i{width:10px;height:10px;border-radius:50%;background:var(--blue);display:block}

.nav{left:0;top:78px;width:711px;height:26px;background:linear-gradient(#fff,#ececec);border-top:1px solid #ddd;border-bottom:1px solid #ccc}
.nav ul{list-style:none;display:flex;position:absolute;left:45px;top:0;height:25px}
.nav li{font-size:8.5px;font-weight:700;color:#222;display:flex;align-items:center;justify-content:center;border-right:1px solid #d6d6d6;height:25px}
.nav li.active{background:var(--green);color:#222}
.subbar{left:45px;top:104px;width:623px;height:22px;background:linear-gradient(#eef78e,var(--green))}

/* feature */
.feature{left:45px;top:140px;width:407px;height:182px;border:1px solid var(--line);background:#fff}
.tick{left:18px;top:14px}
.kicker{font-size:7.5px;color:var(--olive);text-transform:uppercase}
.feature .kicker{position:absolute;left:58px;top:11px}
.feature h1{position:absolute;left:58px;top:23px;width:235px;font-size:14px;font-weight:400;line-height:19px;color:var(--green-dark)}
.meta{position:absolute;left:11px;top:71px;font-size:6.8px;color:#777;line-height:12px;font-weight:700}
.feature p{position:absolute;left:11px;top:105px;width:280px;font-size:7.3px;line-height:11.5px;color:#444}
.more{position:absolute;top:161px;font-size:7px;font-weight:700;color:var(--link)}
.more::before{content:"➜ ";font-size:6px}
.feature-tabs{position:absolute;right:-1px;top:-1px;width:106px;height:182px}
.feature-tab{height:60.6px;background:linear-gradient(var(--blue-light),var(--blue));border-bottom:1px solid #fff;display:flex;align-items:center;gap:8px;padding-left:10px;color:#fff;font-size:15px;line-height:17px}
.feature-tab span.ico{width:22px;height:24px;background:#eef3f8;border:1px solid #c7d6e4;display:block;flex:none}
.feature-tab span.ico.dark{background:#2a2a2a;border-color:#111}

/* ads */
.ad{border:1px solid var(--line);background:#fff}
.ad-label{position:absolute;left:4px;top:3px;font-size:6px;color:#888}
.ad-label::before{content:"› ";color:#c33}
.ad-box{position:absolute;background:linear-gradient(#e8e8e8,var(--ad));color:var(--ad-text);font-size:14px;line-height:16px;padding:3px 5px}

.textads{left:463px;top:330px;width:185px;height:170px;font-size:7.5px;line-height:10px}
.textad{margin-bottom:11px}
.textad b{display:block;color:#1111cc;text-decoration:underline;font-size:8.5px;margin-bottom:1px}
.textad small{display:block;color:#2a8a2a;font-size:6px}
.pager{position:absolute;top:157px;left:1px;display:flex;gap:2px}
.pager i{width:9px;height:9px;display:block;background:#bbc;border:1px solid #99a}
.pager i.on{background:#222299}
.pager i.off{background:#fff}
.textads .pageinput{position:absolute;left:133px;top:150px;width:50px;height:9px;border:1px solid #bbb}

/* section headers */
.section-head{height:32px;background:linear-gradient(#eaf57d,var(--green));color:#3b4a08;font-size:16px;display:flex;align-items:center;padding-left:8px;border-radius:2px}

/* newsletter */
.newsletter{left:464px;top:505px;width:204px}
.newsletter .section-head{font-size:12px;height:31px}
.newsletter p{font-size:7px;line-height:11.5px;color:#555;margin:9px 0 6px 1px}
.newsletter label{display:block;font-size:7.5px;font-weight:700;margin-top:5px;margin-bottom:4px}
.newsletter .field{height:16px;border:1px solid #ddd;background:linear-gradient(#f3f3f3,#fff);margin-bottom:4px}
.newsletter .fine{font-size:7px;line-height:11px;color:#555;margin-top:6px}
.subscribe{display:inline-block;margin-top:8px;background:linear-gradient(#ffc050,var(--orange));color:#fff;font-size:6.5px;font-weight:700;padding:5px 6px;border-radius:2px}

/* news */
.news{left:45px;top:337px;width:407px}
.news .section-head{justify-content:space-between;padding-left:0;padding-right:8px;font-size:16px}
.news .section-head .lead{display:flex;align-items:center;gap:18px}
.news .section-head .lead i{display:block;width:30px;height:30px;background:#eef3f8;border:1px solid #c7d6e4;margin-left:6px}
.rss{width:17px;height:17px;border-radius:3px;background:var(--orange)}
.tabs{display:flex;gap:2px;margin-top:11px;border-bottom:1px solid #ccc}
.tabs li{list-style:none;font-size:8.5px;color:#555;background:linear-gradient(#fafafa,#e2e2e2);border:1px solid #ccc;border-bottom:none;padding:3px 4px 2px}
.tabs li.on{background:linear-gradient(#ffe0a0,#f8c060);color:#333}
.item{display:flex;gap:9px;padding:8px 0 7px;border-bottom:1px solid var(--line)}
.thumb{width:24px;height:26px;flex:none;background:#f0f0f0;border:1px solid #ccc}
.thumb.person{border-radius:50%;background:linear-gradient(#e8b58c,#b07045);border:none}
.item .kicker{display:block;font-size:7.5px;margin-bottom:3px}
.item .kicker em{font-style:normal;color:var(--orange);margin-left:3px}
.item h3{font-size:11px;font-weight:400;line-height:15px;color:var(--link)}
.catlinks{list-style:none;margin-top:9px;border-bottom:1px solid #ddd;padding-bottom:6px}
.catlinks li{font-size:6.5px;font-weight:700;color:var(--link);line-height:11.7px}
.catlinks li::before{content:"➜ ";font-size:6px}

/* bottom columns */
.col{width:197px}
.col h4{font-size:8px;font-weight:700;margin:11px 0 8px}
.col p{font-size:6.7px;line-height:10.5px;color:#555}
.btn-tiles{display:flex;gap:7px;margin-top:10px}
.btn-tile{width:93px;height:78px;background:linear-gradient(var(--blue-light),var(--blue));border-radius:4px;color:#e8f4ff;font-size:9px;font-weight:700;text-align:center;padding-top:48px;line-height:11px;position:relative}
.btn-tile i{position:absolute;left:33px;top:12px;width:28px;height:24px;background:rgba(255,255,255,.55);border-radius:3px}
.btn-tile i.arrow{background:none}
.sub-head{margin-top:12px;height:24px;background:linear-gradient(#fff,#ececec);font-size:14px;color:#333;padding-left:4px;line-height:24px}
.res-list,.forum-list{list-style:none}
.res-list li{font-size:9.5px;color:var(--link);display:flex;align-items:center;gap:7px;margin-top:5.5px;padding-left:1px}
.res-list li i{width:14px;height:14px;border-radius:50%;border:3px solid #aaa;display:block}
.forum-list li{display:flex;gap:8px;font-size:9.5px;font-weight:700;color:var(--link);line-height:12px;margin-bottom:8.5px}
.forum-list li i{width:14px;height:11px;background:var(--green);border-radius:2px;flex:none;margin-top:1px;position:relative}
.forum-list li i::after{content:"";position:absolute;left:6px;top:4px;width:10px;height:8px;background:var(--blue);border-radius:2px}
.see-all{font-size:6.5px;font-weight:700;color:var(--link);margin-top:13px;padding-bottom:6px;border-bottom:1px solid #ddd}
.see-all::before{content:"➜ ";font-size:6px}

/* footer */
.footer{left:0;top:1112px;width:711px;height:88px;background:linear-gradient(#ececec,#fff 40%)}
.footer nav{position:absolute;top:38px;width:100%;text-align:center;font-size:8.2px;color:#444}
.footer nav span{margin:0 5px;color:#888}
.footer .copy{position:absolute;top:64px;width:100%;text-align:center;font-size:8.2px;color:#444}
.footer .copy b{color:#333}
</style>
</head>
<body>
<div class="page">

  <header>
    <div class="abs brand"><span>Plume Harbor</span><span class="brand-dot"></span></div>
    <div class="abs tagline">Helping You Succeed Online</div>
    <div class="abs search"><div class="search-field"></div><div class="search-btn">Site Search</div></div>
    <div class="abs lang"><i></i>English</div>
  </header>

  <nav class="abs nav">
    <ul>
      <li class="active" style="width:54px">Home</li>
      <li style="width:61px">Forums</li>
      <li style="width:58px">Videos</li>
      <li style="width:61px">Articles</li>
      <li style="width:82px">Publications</li>
      <li style="width:57px">SEO Blog</li>
      <li style="width:99px">Marketing Blog</li>
      <li style="width:80px">Resources</li>
      <li style="width:71px;border-right:none">Advertise</li>
    </ul>
  </nav>
  <div class="abs subbar"></div>

  <section class="abs feature">
    <svg class="abs tick" width="30" height="36" viewBox="0 0 30 36"><path d="M2 20 L11 32 L28 3" fill="none" stroke="#5aa321" stroke-width="5" stroke-linecap="round" stroke-linejoin="round"/></svg>
    <span class="kicker">Articles</span>
    <h1>5 Reasons to Build Multiple Niche Websites and Leverage Them</h1>
    <div class="meta">Published on May 14, 2010<br>by Marla Quint</div>
    <p>Multiple niche websites are a great way to cover all aspects of a business and expand your market reach. Having multiple websites which cover a lot of ground for one business is the latest trend in the field of search engine optimization.</p>
    <a class="more" style="left:11px">Read more</a>
    <a class="more" style="left:225px">See all articles</a>
    <div class="feature-tabs">
      <div class="feature-tab"><span class="ico"></span>Articles</div>
      <div class="feature-tab"><span class="ico dark"></span>Videos</div>
      <div class="feature-tab"><span class="ico"></span>Blog<br>posts</div>
    </div>
  </section>

  <aside class="abs ad" style="left:465px;top:140px;width:203px;height:182px">
    <span class="ad-label">Add</span>
    <div class="ad-box" style="left:5px;top:16px;width:192px;height:160px">Medium Rectangle<br>300x250</div>
  </aside>

  <aside class="abs textads">
    <div class="textad"><b>Online Email Marketing</b>Expand Your Business Quickly w/ Our User-Friendly Software! Free Trial.<small>www.Mailvane.com</small></div>
    <div class="textad"><b>Web site not available ?</b>We monitor your web site non-stop. Instant email &amp; sms alert. Reports.<small>www.Uptrellis.com</small></div>
    <div class="textad"><b>Study Digital Marketing</b>Corrow Business Institute Next Round Ends Jun 27th—Apply Now!<small>www.Corrow.edu/masters-program/</small></div>
    <div class="pager"><i></i><i class="on"></i><i class="off"></i></div>
    <div class="pageinput"></div>
  </aside>

  <section class="abs newsletter">
    <div class="section-head">Get The Latest Online Strategies</div>
    <p>Get all the latest webmaster tips and tricks from some of the brightest minds in the online world delivered right to your inbox with the Plume-Harbor Newsletter.</p>
    <label>Last name:</label><div class="field"></div>
    <label style="margin-top:14px">First name:</label><div class="field"></div>
    <label style="margin-top:14px">Your e-mail:</label><div class="field"></div>
    <div class="fine">Your <a>privacy</a> is 100% Guaranteed. Easily <a>unsubscribe</a> at any time.</div>
    <span class="subscribe">SUBSCRIBE ME</span>
  </section>

  <section class="abs news">
    <div class="section-head"><span class="lead"><i></i>News</span><span class="rss"></span></div>
    <ul class="tabs">
      <li class="on">LASTEST</li><li>ARTICLES</li><li>SEO BLOG</li><li>MARKETING BLOG</li><li>VIDEOS</li><li>FORUMS</li><li>RESOURCES</li>
    </ul>
    <div class="item"><div class="thumb person" role="img" aria-label="Author portrait"></div><div><span class="kicker">Blog post <em>SEO BLOG THE EXPERTS SAY...</em></span><h3>Searchly Uses Semantic Closeness as a Ranking Factor</h3></div></div>
    <div class="item"><div class="thumb"></div><div><span class="kicker">Articles</span><h3>Do Not Make These 10 Common SEO Mistakes</h3></div></div>
    <div class="item"><div class="thumb person" role="img" aria-label="Author portrait"></div><div><span class="kicker">Blog post <em>MARKETING BLOG THE EXPERTS SAY...</em></span><h3>Study: Paydrift Reveals Why Consumers Abandon Sites During Checkout</h3></div></div>
    <div class="item"><div class="thumb"></div><div><span class="kicker">Articles</span><h3>Online Reputation Management Advice</h3></div></div>
    <ul class="catlinks">
      <li>SEO Articles</li><li>Internet Marketing Articles</li><li>Development Articles</li><li>General Articles</li><li>And also in our Archives</li>
    </ul>
  </section>

  <aside class="abs ad" style="left:92px;top:690px;width:309px;height:55px">
    <span class="ad-label">Add</span>
    <div class="ad-box" style="left:5px;top:13px;width:297px;height:37px">Full Banner<br>468x60</div>
  </aside>

  <section class="abs col" style="left:45px;top:759px">
    <div class="section-head">Resources</div>
    <h4>Get Listed in the PH Directory Now!</h4>
    <p>If you have a product or service aimed at web professionals, and want to expose yourself to 100,000+ monthly visitors add yourself to the Plume-Harbor directory.</p>
    <div class="btn-tiles">
      <div class="btn-tile"><svg class="abs" style="left:30px;top:10px" width="34" height="28" viewBox="0 0 34 28"><path d="M2 9h18V2l12 12-12 12v-7H2z" fill="#9bd12a" stroke="#6a9a10"/></svg>Submit your bussiness</div>
      <div class="btn-tile"><i></i>More webmaster Resources</div>
    </div>
    <div class="sub-head">Lastest resources</div>
    <ul class="res-list">
      <li><i></i>RSS Parser</li><li><i></i>Keyword Density</li><li><i></i>Verify Your Site</li>
    </ul>
    <div class="see-all" style="margin-top:16px">See all resources</div>
  </section>

  <section class="abs col" style="left:255px;top:759px">
    <div class="section-head">Forums</div>
    <h4>Industry Discussions and Help</h4>
    <ul class="forum-list">
      <li><i></i>Beaten!</li>
      <li><i></i>Need SMTP server for mass emailing</li>
      <li><i></i>Hosting Options</li>
      <li><i></i>Funny Customer Service Inquiries</li>
      <li><i></i>What to do you use to develop websites ?</li>
      <li><i></i>Pressblock Spam</li>
      <li><i></i>PH Directory</li>
      <li><i></i>36 More SEO Myths</li>
      <li><i></i>'Rotating' Newsboard &amp; SEO</li>
      <li><i></i>Searchly's new look</li>
    </ul>
    <div class="see-all" style="margin-top:2px">See all discussions</div>
  </section>

  <aside class="abs ad" style="left:464px;top:763px;width:204px;height:83px">
    <span class="ad-label">Add</span>
    <div class="ad-box" style="left:5px;top:13px;width:194px;height:64px">3:1 Rectangle<br>300x100</div>
  </aside>
  <aside class="abs ad" style="left:464px;top:861px;width:204px;height:57px">
    <span class="ad-label">Add</span>
    <div class="ad-box" style="left:27px;top:13px;width:150px;height:38px">Half Banner<br>234x60</div>
  </aside>
  <aside class="abs ad" style="left:464px;top:934px;width:204px;height:57px">
    <span class="ad-label">Add</span>
    <div class="ad-box" style="left:61px;top:13px;width:78px;height:38px">Button 2<br>120x60</div>
  </aside>
  <aside class="abs ad" style="left:464px;top:1007px;width:204px;height:77px">
    <span class="ad-label">Add</span>
    <div class="ad-box" style="left:61px;top:13px;width:78px;height:58px">Button 1<br>120x90</div>
  </aside>

  <footer class="abs footer">
    <nav>Home<span>|</span>Forums<span>|</span>Videos<span>|</span>Articles<span>|</span>Publications<span>|</span>SEO Blog<span>|</span>Marketing Blog<span>|</span>Resources<span>|</span>Advertise<span>|</span>RSS Feeds<span>|</span>Contact Us</nav>
    <div class="copy">Copyright 2004 - 2010 Plume-Harbor.com &nbsp;| <b>Privacy Policy</b> | <b>Affiliate Disclaimer</b></div>
  </footer>

</div>
</body>
</html>
```